Business card design for Automotive workshop

We need a business card for a new automotive repair and tyre shop called Keelstone Prime Automotive located in New Zealand. We are a clean, modern and fresh workshop and company.

Front needs to feature logo,
my name:
Marlo Fenwicke (director)

Address:
48 Tarn Lane
Koruwai 3586

Phone: 07 594 2713
Mobile: 027 451 9362
Email: office@keelstoneautomotive.example.nz
Website: keelstoneautomotive.example.nz

Back needs to feature an area to write down appointment details, date and time.

Also feature a list of jobs and work we do such as,
Vehicle Servicing
All Mechanical Repairs
Warrant of Fitness
Tyres & Wheel Alignments
Automotive Diagnostics
Automotive Parts & Supplies

```html
<!DOCTYPE html>
<html lang="en">
<head>
<meta charset="utf-8">
<title>Keelstone Prime Automotive — Business Card</title>
<link rel="stylesheet" href="https://fonts.googleapis.com/css2?family=Saira:wght@400;600;800&display=swap">
<style>
  :root {
    --red: #e31e24;
    --black: #121212;
    --ink: #1d1d1f;
    --white: #ffffff;
    --stage: #2b2d31;
    --dash: #6b6b6b;
  }
  * { margin: 0; padding: 0; box-sizing: border-box; }
  html, body { width: 1200px; height: 900px; overflow: hidden; }
  body {
    background: var(--stage);
    font-family: "Saira", Arial, sans-serif;
    color: var(--ink);
    position: relative;
  }
  .card {
    position: absolute;
    left: 280px;
    width: 640px;
    height: 366px;
    background: var(--white);
    overflow: hidden;
  }
  .card--front { top: 46px; }
  .card--back { top: 470px; }

  .card__art { position: absolute; inset: 0; }

  .brand-name {
    position: absolute;
    font-weight: 800;
    color: var(--red);
    text-transform: uppercase;
    letter-spacing: 1px;
    line-height: 1.05;
    text-align: right;
  }

  /* Front */
  .card--front .brand-name {
    right: 34px;
    top: 100px;
    font-size: 27px;
  }
  .contact-block {
    position: absolute;
    left: 255px;
    top: 176px;
  }
  .person-name {
    font-size: 24px;
    font-weight: 800;
    color: var(--red);
    text-transform: uppercase;
    letter-spacing: 1px;
    line-height: 1;
  }
  .person-role {
    font-size: 15px;
    margin-top: 2px;
    margin-bottom: 8px;
  }
  .contact-list { list-style: none; }
  .contact-list li {
    display: flex;
    align-items: center;
    gap: 8px;
    font-size: 14.5px;
    line-height: 20px;
  }
  .contact-list svg { width: 13px; height: 13px; flex: none; }
  .address {
    margin-top: 8px;
    font-size: 15px;
    color: var(--red);
  }

  /* Back */
  .card--back .brand-name {
    right: 30px;
    top: 26px;
    font-size: 25px;
    color: var(--red);
  }
  .service-list {
    position: absolute;
    list-style: none;
    font-size: 13px;
    text-transform: uppercase;
    line-height: 17px;
    letter-spacing: 0.5px;
  }
  .service-list li { display: flex; align-items: center; gap: 7px; }
  .service-list--left li::before,
  .service-list--right li::after {
    content: "";
    width: 7px; height: 7px;
    border-radius: 50%;
    background: var(--red);
    flex: none;
  }
  .service-list--left { left: 24px; top: 26px; }
  .service-list--right { right: 24px; top: 128px; }
  .service-list--right li { justify-content: flex-end; }

  .write-line {
    position: absolute;
    display: flex;
    align-items: flex-end;
    gap: 6px;
    height: 18px;
    font-size: 13px;
    text-transform: uppercase;
  }
  .write-line::after {
    content: "";
    flex: 1;
    border-bottom: 1.5px dashed var(--dash);
    margin-bottom: 4px;
  }
  .write-line--blank { left: 24px; width: 300px; top: 124px; }
  .write-line--date { left: 24px; width: 300px; top: 168px; }
  .write-line--mid { left: 24px; right: 24px; top: 216px; }
  .write-line--time { left: 354px; right: 24px; top: 266px; }
  .write-line--end { left: 24px; right: 24px; top: 316px; }
</style>
</head>
<body>

<section class="card card--front" aria-label="Business card front">
  <svg class="card__art" viewBox="0 0 640 366" aria-hidden="true">
    <line x1="0" y1="58" x2="640" y2="58" stroke="#121212" stroke-width="1.2"/>
    <line x1="0" y1="66" x2="640" y2="66" stroke="#e31e24" stroke-width="1.2"/>
  </svg>

  <div class="brand-name">Keelstone Prime<br>Automotive</div>

  <div class="contact-block">
    <div class="person-name">Marlo Fenwicke</div>
    <div class="person-role">Director</div>
    <ul class="contact-list">
      <li>
        <svg viewBox="0 0 16 16"><circle cx="8" cy="8" r="7" fill="none" stroke="#e31e24" stroke-width="1.4"/><path d="M5.5 4.5l1.5 0 .7 2-1 .8a5 5 0 0 0 2 2l.8-1 2 .7v1.5c-3.5.3-6.3-2.5-6-6z" fill="#e31e24"/></svg>
        07 594 2713
      </li>
      <li>
        <svg viewBox="0 0 16 16"><rect x="4" y="1" width="8" height="14" rx="1.5" fill="none" stroke="#e31e24" stroke-width="1.5"/><circle cx="8" cy="12.5" r="0.9" fill="#e31e24"/></svg>
        027 451 9362
      </li>
      <li>
        <svg viewBox="0 0 16 16"><rect x="1" y="3" width="14" height="10" fill="none" stroke="#e31e24" stroke-width="1.5"/><path d="M1 3l7 6 7-6" fill="none" stroke="#e31e24" stroke-width="1.5"/></svg>
        office@keelstoneautomotive.example.nz
      </li>
      <li>
        <svg viewBox="0 0 16 16"><circle cx="8" cy="8" r="7" fill="none" stroke="#e31e24" stroke-width="1.4"/><ellipse cx="8" cy="8" rx="3" ry="7" fill="none" stroke="#e31e24" stroke-width="1.2"/><line x1="1" y1="8" x2="15" y2="8" stroke="#e31e24" stroke-width="1.2"/></svg>
        keelstoneautomotive.example.nz
      </li>
    </ul>
    <div class="address">48 Tarn Lane, Koruwai 3586</div>
  </div>
</section>

<section class="card card--back" aria-label="Business card back">
  <svg class="card__art" viewBox="0 0 640 366" aria-hidden="true">
    <polygon points="0,0 250,0 0,14" fill="#e31e24"/>
    <polygon points="290,0 640,0 640,108 214,108" fill="#121212"/>
  </svg>

  <div class="brand-name">Keelstone Prime<br>Automotive</div>

  <ul class="service-list service-list--left">
    <li>Vehicle Servicing</li>
    <li>All Mechanical Repairs</li>
    <li>Warrant of Fitness</li>
  </ul>

  <div class="write-line write-line--blank"></div>
  <div class="write-line write-line--date">Date:</div>
  <div class="write-line write-line--mid"></div>
  <div class="write-line write-line--time">Time:</div>
  <div class="write-line write-line--end"></div>

  <ul class="service-list service-list--right">
    <li>Tyres &amp; Wheel Alignments</li>
    <li>Automotive Diagnostics</li>
    <li>Automotive Parts &amp; Supplies</li>
  </ul>
</section>

</body>
</html>
```